Quillbrook IT company focused on 3 areas of IT

Looking for something similar to attached cards. Logo for quillbrook also attached.. Looking for something clean as far as colors (surprise me).. Quill stands for 3 primary areas, web design, consulting and network infrastructure design. Please email me if you have any questions. Looking forward to seeing how creative and professional this card will look. Thank you,

Target Market(s)

Small business/consumers looking for It services

Industry/Entity Type

It Service

Contact Information for Business Card

Dorin Vasek
Principal Consultant

202-555-0173

www.quillbrook-example.com
dvasek@quillbrook-example.com

27416 Copper Lantern Way,
Ashvale, MD 20999

Colors

Designer to choose colors to be used in the design.

Requirements
Must have
• attached Logo design. Feel free to play with the colors.. If you have a better idea for a card, please fee free to send me. Looking for something clean/modern. Should have tech feel, not cheesy.
Nice to have
• Surprise me :-)..

```html
<!DOCTYPE html>
<html lang="en">
<head>
<meta charset="utf-8">
<title>Quillbrook Business Card</title>
<link rel="stylesheet" href="https://fonts.googleapis.com/css2?family=Montserrat:wght@500&family=Work+Sans:wght@400;600&display=swap">
<style>
  :root {
    --bg: #2a2a2b;
    --card: #1c1c1d;
    --card-edge: #242425;
    --accent: #1fa3e0;
    --ink: #f2f2f2;
    --foil: #8d8d90;
  }
  * { margin: 0; padding: 0; box-sizing: border-box; }
  html, body { width: 1200px; height: 900px; overflow: hidden; }
  body {
    background: var(--bg);
    display: flex;
    flex-direction: column;
    align-items: center;
    justify-content: center;
    gap: 40px;
    font-family: "Work Sans", sans-serif;
  }
  .card {
    width: 700px;
    height: 400px;
    background: linear-gradient(135deg, var(--card) 0%, var(--card-edge) 100%);
    position: relative;
  }
  .card-front {
    display: flex;
    align-items: center;
    justify-content: center;
  }
  .wordmark-foil {
    font-weight: 600;
    font-size: 64px;
    color: var(--foil);
    letter-spacing: 1px;
  }
  .card-back {
    display: flex;
    align-items: center;
  }
  .brand {
    width: 300px;
    display: flex;
    justify-content: center;
  }
  .wordmark {
    font-weight: 600;
    font-size: 40px;
    color: var(--accent);
  }
  .divider {
    width: 2px;
    height: 190px;
    background: var(--ink);
  }
  .details {
    padding-left: 40px;
    color: var(--ink);
  }
  .name {
    font-family: "Montserrat", sans-serif;
    font-weight: 500;
    font-size: 34px;
    color: var(--accent);
    letter-spacing: 1px;
    line-height: 1;
  }
  .role { font-size: 18px; letter-spacing: 0.5px; margin-top: 4px; }
  .address { font-size: 17px; letter-spacing: 0.5px; line-height: 1.35; margin-top: 14px; }
  .contacts { list-style: none; margin-top: 12px; font-size: 17px; letter-spacing: 0.5px; line-height: 1.4; }
  .contacts li { display: flex; align-items: center; gap: 10px; }
  .contacts svg { width: 12px; height: 12px; flex: none; }
</style>
</head>
<body>
  <section class="card card-front">
    <span class="wordmark-foil">Quillbrook</span>
  </section>

  <section class="card card-back">
    <div class="brand"><span class="wordmark">Quillbrook</span></div>
    <div class="divider"></div>
    <div class="details">
      <h1 class="name">DORIN VASEK</h1>
      <p class="role">Principal Consultant</p>
      <p class="address">27416 Copper Lantern Way,<br>Ashvale, MD 20999</p>
      <ul class="contacts">
        <li>
          <svg viewBox="0 0 12 12" aria-hidden="true"><path d="M3 1 L5 3.5 L4 5 Q5.5 7.5 7 8 L8.5 7 L11 9 L9.5 11 Q4 10 1 3 Z" fill="none" stroke="var(--accent)" stroke-width="1.2"/></svg>
          202-555-0173
        </li>
        <li>
          <svg viewBox="0 0 12 12" aria-hidden="true"><rect x="1" y="2.5" width="10" height="7" fill="none" stroke="var(--accent)" stroke-width="1.2"/><path d="M1 2.5 L6 6.5 L11 2.5" fill="none" stroke="var(--accent)" stroke-width="1.2"/></svg>
          dvasek@quillbrook-example.com
        </li>
        <li>
          <svg viewBox="0 0 12 12" aria-hidden="true"><circle cx="6" cy="6" r="5" fill="none" stroke="var(--accent)" stroke-width="1.2"/><ellipse cx="6" cy="6" rx="2.2" ry="5" fill="none" stroke="var(--accent)" stroke-width="1"/><path d="M1 6 H11" stroke="var(--accent)" stroke-width="1"/></svg>
          www.quillbrook-example.com
        </li>
      </ul>
    </div>
  </section>
</body>
</html>
```